Tech Savy small Business accountant business card design

We need a business card for a new company based in the cloud. We provide tax, business advisory, accounting, information technology solutions and back office functions to small businesses. We offer fixed fee packages with add on services as you need them. By harnessing technology we simplify small business operational processes providing valuable time and information for small business owners to grow their business. In the logo (bluvoria) we want to be able to see bluv and experts. The final design should communicate achieving growth dreams and balance (ie life and $).
Updates
This project has been temporarily placed on hold until I finalize "Tech Savy small Business accountant needs a logo". I invite all designers to submit on this logo project. Once my logo is finalized I will resume this business card contest. Thanks Added Wednesday, March 19, 2014
This project has been temporarily placed on hold until I finalize "Tech Savy small Business accountant logo". I invite all designers to submit on this logo project. Once my logo is finalized I will resume this business card contest. Thanks Added Thursday, March 20, 2014
Target Market(s)
Small Business (Revenue $500,000, more than 3 employees) owners.
Industry/Entity Type
Small Business
Contact Information for Business Card
Marcy Elwind (Principal)
Accountant, Tax Agent.
TEL | 0417 683 912
EMAIL | Marcy.Elwind@bluvoria.com.au
WEB | www.bluvoria.com.au
Look and feel

```html
<!DOCTYPE html>
<html lang="en">
<head>
<meta charset="utf-8">
<title>bluvoria business card</title>
<link rel="stylesheet" href="https://fonts.googleapis.com/css2?family=Open+Sans:wght@400;600;700&display=swap">
<style>
  :root {
    --page-bg: #ecedef;
    --card-white: #ffffff;
    --brand-blue: #1c7cc2;
    --blue-deep: #1768b3;
    --blue-light: #3eaee3;
    --swoosh-grey: #a3a6aa;
    --tagline-grey: #6b6e72;
    --text-white: #ffffff;
    --card-shadow: rgba(0, 0, 0, 0.18);
  }
  * { margin: 0; padding: 0; box-sizing: border-box; }
  html, body {
    width: 1200px;
    height: 913px;
    overflow: hidden;
    background: var(--page-bg);
    font-family: "Open Sans", Arial, sans-serif;
  }
  .stage {
    position: relative;
    width: 1200px;
    height: 913px;
  }
  .card {
    position: absolute;
    top: 302px;
    width: 540px;
    height: 309px;
    border-radius: 16px;
    overflow: hidden;
    background: var(--card-white);
    box-shadow: 0 10px 28px var(--card-shadow);
  }
  .card--front { left: 40px; }
  .card--back { left: 620px; }
  .card__art {
    position: absolute;
    inset: 0;
    width: 100%;
    height: 100%;
  }
  .brand {
    position: absolute;
    white-space: nowrap;
  }
  .brand__name {
    display: block;
    font-weight: 700;
    color: var(--brand-blue);
    letter-spacing: -1px;
    line-height: 1;
  }
  .brand__tagline {
    display: block;
    font-weight: 600;
    color: var(--tagline-grey);
    line-height: 1.2;
  }
  .card--front .brand { left: 58px; top: 44px; }
  .card--front .brand__name { font-size: 58px; }
  .card--front .brand__tagline { font-size: 15px; margin-top: 4px; padding-left: 6px; }
  .card--back .brand { left: 96px; top: 104px; }
  .card--back .brand__name { font-size: 70px; }
  .card--back .brand__tagline { font-size: 18px; margin-top: 4px; padding-left: 10px; }
  .holder {
    position: absolute;
    left: 30px;
    bottom: 20px;
    color: var(--text-white);
    text-align: right;
  }
  .holder__name { font-size: 15px; font-weight: 700; letter-spacing: 0.3px; }
  .holder__role { font-size: 12px; font-weight: 400; }
  .contacts {
    position: absolute;
    right: 22px;
    bottom: 30px;
    list-style: none;
    color: var(--text-white);
    font-size: 11.5px;
    line-height: 18px;
  }
  .contacts__item { display: flex; align-items: center; gap: 7px; }
  .contacts__icon { width: 12px; height: 12px; flex: none; }
</style>
</head>
<body>
<main class="stage">
  <section class="card card--front" aria-label="Card front">
    <svg class="card__art" viewBox="0 0 540 309" aria-hidden="true">
      <defs>
        <linearGradient id="bandBlue" x1="0" y1="1" x2="1" y2="0">
          <stop offset="0" stop-color="var(--blue-deep)"/>
          <stop offset="1" stop-color="var(--blue-light)"/>
        </linearGradient>
      </defs>
      <path d="M0,236 Q420,244 540,30 L540,309 L0,309 Z" fill="url(#bandBlue)"/>
      <path d="M0,231 Q416,239 538,22" fill="none" stroke="var(--swoosh-grey)" stroke-width="6"/>
    </svg>
    <div class="brand">
      <span class="brand__name">bluvoria</span>
      <span class="brand__tagline">Your business and accounting partner</span>
    </div>
    <ul class="contacts">
      <li class="contacts__item">
        <svg class="contacts__icon" viewBox="0 0 12 12"><path d="M3 1 L5 3.5 L4 5 Q5 7 7 8 L8.5 7 L11 9 L10 11 Q5 11 1 6 Q1 3 3 1Z" fill="var(--text-white)"/></svg>
        0417 683 912
      </li>
      <li class="contacts__item">
        <svg class="contacts__icon" viewBox="0 0 12 12"><circle cx="6" cy="6" r="5" fill="none" stroke="var(--text-white)" stroke-width="1.2"/><ellipse cx="6" cy="6" rx="2.2" ry="5" fill="none" stroke="var(--text-white)" stroke-width="1"/><line x1="1" y1="6" x2="11" y2="6" stroke="var(--text-white)" stroke-width="1"/></svg>
        www.bluvoria.com.au
      </li>
      <li class="contacts__item">
        <svg class="contacts__icon" viewBox="0 0 12 12"><rect x="1" y="2.5" width="10" height="7" fill="none" stroke="var(--text-white)" stroke-width="1.2"/><path d="M1 2.5 L6 7 L11 2.5" fill="none" stroke="var(--text-white)" stroke-width="1.2"/></svg>
        Marcy.Elwind@bluvoria.com.au
      </li>
    </ul>
    <div class="holder">
      <p class="holder__name">MARCY ELWIND (Principal)</p>
      <p class="holder__role">Accountant, Tax Agent</p>
    </div>
  </section>

  <section class="card card--back" aria-label="Card back">
    <div class="brand">
      <span class="brand__name">bluvoria</span>
      <span class="brand__tagline">Your business and accounting partner</span>
    </div>
  </section>
</main>
</body>
</html>
```